New bussiness card, using company logo.
Lionel Brisk
Manager/Director
Brisk Property Developments
Po Box 5347
Wattlebrook Central
Wbk
0491 638 205
lionel@briskpropertydevelopments
eye catching, vibrant colours, professional

```html
<!DOCTYPE html>
<html lang="en">
<head>
<meta charset="utf-8">
<title>Brisk Property Developments – Business Cards</title>
<link rel="stylesheet" href="https://fonts.googleapis.com/css2?family=Exo+2:wght@400;600;700&family=Open+Sans:wght@400;600&display=swap">
<style>
  :root {
    --green: #6cbd45;
    --green-light: #8cc63f;
    --red: #e0252b;
    --white: #ffffff;
    --ink: #4a4a4a;
    --grey-line: #c8c8c8;
    --stage: #e9e6e2;
  }
  * { box-sizing: border-box; margin: 0; padding: 0; }
  html, body { width: 1200px; height: 746px; overflow: hidden; }
  body {
    background: var(--stage);
    position: relative;
    font-family: "Open Sans", Arial, sans-serif;
  }
  .card {
    position: absolute;
    width: 525px;
    height: 298px;
    overflow: hidden;
    box-shadow: 0 2px 6px rgba(0,0,0,.25);
  }
  .card--front { left: 45px; top: 35px; background: var(--white); }
  .card--back-white { left: 611px; top: 40px; background: var(--white); }
  .card--back-green { left: 48px; top: 394px; background: linear-gradient(180deg, var(--green) 0%, var(--green-light) 100%); }
  .card--back-red { left: 627px; top: 394px; background: var(--red); }

  /* front card */
  .band {
    position: absolute; left: 0; width: 100%; height: 33px;
    background: linear-gradient(90deg, var(--green) 0%, var(--green-light) 100%);
    color: var(--white);
    display: flex; align-items: center; justify-content: center;
    white-space: nowrap;
  }
  .band--top { top: 0; }
  .band--bottom { bottom: 0; font-size: 13px; letter-spacing: 1px; }
  .holder-name { font-weight: 600; font-size: 17px; }
  .holder-role { font-size: 14px; margin-left: 5px; }
  .rule { position: absolute; left: 0; width: 100%; height: 2px; background: var(--red); }
  .rule--top { top: 37px; }
  .rule--bottom { bottom: 38px; }
  .rule::after {
    content: ""; position: absolute; left: 0; right: 0; top: 4px; height: 1px; background: var(--grey-line);
  }
  .rule--bottom::after { top: -5px; }

  .brand {
    position: absolute; left: 0; right: 0;
    display: flex; align-items: center; justify-content: center; gap: 10px;
    font-family: "Exo 2", Arial, sans-serif; font-weight: 700;
    text-transform: uppercase; letter-spacing: .5px;
    white-space: nowrap;
  }
  .brand__mark { width: 18px; height: 18px; flex: none; }
  .card--front .brand { top: 120px; font-size: 24px; color: var(--red); }
  .card--front .brand__mark { background: var(--green); }
  .card--back-white .brand { top: 160px; font-size: 26px; color: var(--green); }
  .card--back-white .brand__mark { background: var(--green); }
  .card--back-green .brand,
  .card--back-red .brand { top: 160px; font-size: 26px; color: var(--white); }
  .card--back-green .brand__mark,
  .card--back-red .brand__mark { background: var(--white); }

  .contact {
    position: absolute; top: 226px; left: 0; right: 0;
    display: flex; justify-content: center; gap: 14px;
    font-size: 12.5px; color: var(--ink); white-space: nowrap;
  }
  .contact__item { display: flex; align-items: center; gap: 5px; }
  .contact__item svg { width: 11px; height: 11px; fill: var(--ink); }

  .web {
    position: absolute; left: 0; right: 0; text-align: center;
    font-family: "Exo 2", Arial, sans-serif; font-size: 14px; letter-spacing: 3px;
    white-space: nowrap;
  }
  .card--back-white .web { top: 250px; color: #333; }
  .web__name { color: var(--red); }
  .web__suffix { color: var(--green); }
  .card--back-green .web,
  .card--back-red .web { top: 254px; color: var(--white); }
</style>
</head>
<body>

  <section class="card card--front">
    <div class="band band--top"><span class="holder-name">Lionel Brisk,</span><span class="holder-role">Manager/Director</span></div>
    <div class="rule rule--top"></div>
    <div class="brand"><span class="brand__mark"></span>Brisk Property Developments</div>
    <div class="contact">
      <span class="contact__item">
        <svg viewBox="0 0 24 24" aria-hidden="true"><path d="M6.6 10.8a15 15 0 0 0 6.6 6.6l2.2-2.2c.3-.3.7-.4 1-.2 1.1.4 2.3.6 3.6.6.6 0 1 .4 1 1V20c0 .6-.4 1-1 1A17 17 0 0 1 3 4c0-.6.4-1 1-1h3.5c.6 0 1 .4 1 1 0 1.3.2 2.5.6 3.6.1.3 0 .7-.2 1z"/></svg>
        0491 638 205
      </span>
      <span class="contact__item">
        <svg viewBox="0 0 24 24" aria-hidden="true"><path d="M2 5h20v14H2zm2 2v.5l8 5 8-5V7l-8 5z"/></svg>
        lionel@briskpropertydevelopments.com
      </span>
    </div>
    <div class="rule rule--bottom"></div>
    <div class="band band--bottom">Po Box 5347, Wattlebrook Central , Wbk</div>
  </section>

  <section class="card card--back-white">
    <div class="brand"><span class="brand__mark"></span>Brisk Property Developments</div>
    <p class="web">www.<span class="web__name">brisk</span><span class="web__suffix">propertydevelopments</span>.com</p>
  </section>

  <section class="card card--back-green">
    <div class="brand"><span class="brand__mark"></span>Brisk Property Developments</div>
    <p class="web">www.briskpropertydevelopments.com</p>
  </section>

  <section class="card card--back-red">
    <div class="brand"><span class="brand__mark"></span>Brisk Property Developments</div>
    <p class="web">www.briskpropertydevelopments.com</p>
  </section>

</body>
</html>
```